Maris Dovey Studio Business Cards

Hi - using the information and logo provided I require a two sided business card designed with the following information. The business card is a 'mini card' 3.5" x 1.25".

Front of card should be the logo attached but inverted (so the background is the peach colour and the logo white).

Back should have these details. If we can't fit the Pictogrum and Friendwall part can we just put the little logos.

Tessa Varnold

Art and Design Consultant
Dealer - Curator - Events - Styling - Creative Sourcing

P: 0438 217 604
E: tessa@marisdoveystudio.example
W: www.marisdoveystudio.example
I (pictogram image please): marisdoveystudio F (Friendwall image please): MarisDoveyAdviser

Target Market(s)

Galleries, artists, art buyers, interior design clients, event managers, creative types

Industry/Entity Type

Business

```html
<!DOCTYPE html>
<html lang="en">
<head>
<meta charset="utf-8">
<title>Maris Dovey Studio – Business Cards</title>
<link rel="stylesheet" href="https://fonts.googleapis.com/css2?family=Cinzel:wght@400&family=Rosario:wght@400;500&display=swap">
<style>
  :root {
    --backdrop: #6f615a;
    --card-front: #121212;
    --card-back: #333333;
    --peach: #f2b8a0;
    --brand-grey: #8d8d8d;
    --ink-light: #f4f1ee;
    --rule-dark: #3a3a3a;
  }
  * { margin: 0; padding: 0; box-sizing: border-box; }
  html, body {
    width: 1200px; height: 960px; overflow: hidden;
    background: var(--backdrop);
  }
  .canvas { position: relative; width: 1200px; height: 960px; }

  .card { position: absolute; box-shadow: 0 14px 22px rgba(0,0,0,.35); }
  .card--front { left: 60px; top: 78px; width: 834px; height: 296px; background: var(--card-front); }
  .card--back  { left: 302px; top: 480px; width: 834px; height: 298px; background: var(--card-back); }

  .brand-mark {
    position: absolute; border-radius: 50%; background: var(--peach);
  }
  .brand-name {
    position: absolute; font-family: "Cinzel", serif; font-weight: 400;
    color: var(--peach); white-space: nowrap; text-align: center;
  }

  /* Front */
  .card--front .brand-mark { left: 357px; top: 22px; width: 120px; height: 120px; }
  .card--front .brand-name { left: 0; width: 834px; top: 156px; font-size: 30px; letter-spacing: 5px; }
  .service-band {
    position: absolute; left: 0; width: 834px; top: 242px; height: 36px;
    border-top: 1px solid var(--rule-dark); border-bottom: 1px solid var(--rule-dark);
    font-family: "Cinzel", serif; font-size: 21px; letter-spacing: 2.5px;
    color: var(--ink-light); text-align: center; line-height: 34px; white-space: nowrap;
  }

  /* Back */
  .card--back .brand-mark { left: 98px; top: 28px; width: 126px; height: 126px; }
  .card--back .brand-name { left: 20px; width: 282px; top: 162px; font-size: 20px; letter-spacing: 2px; }
  .contact-block { position: absolute; left: 372px; top: 24px; width: 432px; font-family: "Rosario", sans-serif; color: var(--ink-light); }
  .person-name { font-size: 42px; font-weight: 500; line-height: 46px; }
  .person-role { font-size: 19px; line-height: 22px; }
  .rule { position: absolute; height: 2px; background: var(--peach); }
  .rule--short { left: 372px; top: 101px; width: 430px; }
  .rule--long { left: 34px; top: 226px; width: 768px; }
  .contact-list { position: absolute; left: 372px; top: 120px; list-style: none; font-family: "Rosario", sans-serif; font-size: 18px; line-height: 30px; color: var(--ink-light); }
  .social-row { position: absolute; left: 0; top: 240px; width: 834px; height: 36px; font-family: "Rosario", sans-serif; font-size: 23px; color: var(--ink-light); }
  .social-item { position: absolute; top: 0; display: flex; align-items: center; gap: 14px; height: 36px; white-space: nowrap; }
  .social-item--pictogram { left: 48px; }
  .social-item--friendwall { left: 478px; }
  .social-square { width: 30px; height: 30px; background: var(--ink-light); }
  .social-divider { position: absolute; left: 406px; top: 6px; width: 1px; height: 24px; background: var(--ink-light); }
</style>
</head>
<body>
<main class="canvas">
  <section class="card card--front" aria-label="Card front">
    <div class="brand-mark"></div>
    <p class="brand-name">MARIS DOVEY STUDIO</p>
    <p class="service-band">Dealer | Curator | Events | Styling | Creative Sourcing</p>
  </section>

  <section class="card card--back" aria-label="Card back">
    <div class="brand-mark"></div>
    <p class="brand-name">MARIS DOVEY STUDIO</p>
    <div class="contact-block">
      <h1 class="person-name">Tessa Varnold</h1>
      <p class="person-role">Art and Design Consultant</p>
    </div>
    <div class="rule rule--short"></div>
    <ul class="contact-list">
      <li>Phone: 0438 217 604</li>
      <li>Email: tessa@marisdoveystudio.example</li>
      <li>Web: www.marisdoveystudio.example</li>
    </ul>
    <div class="rule rule--long"></div>
    <div class="social-row">
      <div class="social-item social-item--pictogram"><span class="social-square"></span><span>MarisDoveyAdviser</span></div>
      <span class="social-divider"></span>
      <div class="social-item social-item--friendwall"><span class="social-square"></span><span>marisdoveystudio</span></div>
    </div>
  </section>
</main>
</body>
</html>
```